Banner (Template) Landing/Home Page PICTURE for my new business

I want a website Banner/ Landing/Home page / Template/ intended for a website I'm starting soon. Is this possible to have this picture and keep it for my future website? I am not completely ready to make website yet so I want an Banner.
The company will be relateed to indoor air quality & energy management controls & solutions . I like IAQ14 pic with windows and reflection of sky and trees. If IAQ14 could be put into IAQ 20, that would be interesting.with a green building or green city such as IAQ10.. See pics for example..Company name & design logo

Target Market(s)

Homeowners and building operators

Industry/Entity Type

Technical Service

Number of Pages Required

1 page

Font styles to use
Serif

Requirements
Must have
• Company Name: Quillbrook Thermal Regulators & Services
Nice to have
• Testing Cleaning, & Controlling Your Air
• Copy of a Logo
• Mobile Web Picture
Should not have
• Your initial designs are okay to use my pics as samples. But the final product I want something creative but yet similar..Not a replica of sample pic with my company name on it

```html
<!DOCTYPE html>
<html lang="en">
<head>
<meta charset="utf-8">
<title>Quillbrook Thermal Regulators &amp; Services</title>
<link rel="stylesheet" href="https://fonts.googleapis.com/css2?family=Roboto+Slab:wght@400;500;700&display=swap">
<style>
  :root {
    --wall: #e4e4e2;
    --sky-deep: #3f82cc;
    --sky-light: #b9d5ee;
    --grass: #5aa82a;
    --grass-deep: #4b9621;
    --floor: #d2d2d0;
    --floor-light: #e8e8e6;
    --haze: rgba(200, 200, 198, 0.5);
    --bubble: rgba(40, 40, 40, 0.82);
    --text-light: #ffffff;
    --divider: #1a1a1a;
    --dot-active: #111111;
  }
  * { box-sizing: border-box; margin: 0; padding: 0; }
  html, body { width: 1200px; height: 720px; overflow: hidden; background: #ffffff; }
  .banner {
    position: relative;
    width: 1200px;
    height: 720px;
    overflow: hidden;
    font-family: "Roboto Slab", serif;
  }
  .scene {
    position: absolute;
    top: 0;
    width: 600px;
    height: 720px;
  }
  .scene--clean {
    left: 600px;
    background: linear-gradient(180deg,
      var(--wall) 0%,
      var(--sky-deep) 18%,
      var(--sky-light) 42%,
      var(--grass) 52%,
      var(--grass-deep) 60%,
      var(--floor) 70%,
      var(--floor-light) 100%);
  }
  .scene--dusty {
    left: 0;
    background:
      linear-gradient(var(--haze), var(--haze)),
      linear-gradient(180deg,
        var(--wall) 0%,
        var(--wall) 18%,
        var(--sky-deep) 32%,
        var(--sky-light) 44%,
        var(--grass) 54%,
        var(--grass-deep) 64%,
        var(--floor) 74%,
        var(--floor-light) 100%);
  }
  .divider {
    position: absolute;
    left: 600px;
    top: 0;
    width: 1px;
    height: 720px;
    background: var(--divider);
  }
  .brand {
    position: absolute;
    left: 32px;
    top: 22px;
    color: var(--text-light);
  }
  .brand__mark {
    font-weight: 700;
    font-size: 78px;
    line-height: 1;
    letter-spacing: -1px;
  }
  .brand__name {
    margin-top: 12px;
    font-weight: 400;
    font-size: 14px;
    line-height: 1.3;
    width: 200px;
  }
  .state {
    position: absolute;
    top: 240px;
    width: 240px;
    height: 240px;
    border-radius: 50%;
    background: var(--bubble);
    display: flex;
    align-items: center;
    justify-content: center;
    color: var(--text-light);
    font-weight: 500;
    font-size: 29px;
  }
  .state--dusty { left: 180px; }
  .state--clean { left: 780px; }
  .pager {
    position: absolute;
    top: 666px;
    left: 560px;
    display: flex;
    gap: 14px;
  }
  .pager__dot {
    width: 17px;
    height: 17px;
    border-radius: 50%;
    background: var(--text-light);
  }
  .pager__dot--active { background: var(--dot-active); }
  .slide-code {
    position: absolute;
    right: 22px;
    top: 666px;
    color: var(--text-light);
    font-size: 13px;
  }
</style>
</head>
<body>
  <section class="banner">
    <div class="scene scene--dusty" role="img" aria-label="Bright empty room with large windows onto blue sky and green lawn, hazy with dust"></div>
    <div class="scene scene--clean" role="img" aria-label="The same bright room with clear air, blue sky and green lawn through the windows"></div>
    <div class="divider"></div>

    <header class="brand">
      <div class="brand__mark">QTRS</div>
      <p class="brand__name">Quillbrook Thermal<br>Regulators &amp; Services</p>
    </header>

    <div class="state state--dusty">Dusty</div>
    <div class="state state--clean">Clean</div>

    <nav class="pager" aria-label="Slides">
      <span class="pager__dot pager__dot--active"></span>
      <span class="pager__dot"></span>
      <span class="pager__dot"></span>
    </nav>

    <span class="slide-code">C5</span>
  </section>
</body>
</html>
```